Tall Fern Roofing Business Card

Need a business card with the logo that was designed here

Contact Information for Business Card

Name, Title, Phone, Email, Website, Company name

```html
<!DOCTYPE html>
<html lang="en">
<head>
<meta charset="UTF-8">
<title>Tall Fern Roofing – Business Card</title>
<link href="https://fonts.googleapis.com/css2?family=Montserrat:wght@800&family=Poppins:wght@400;500;600&display=swap" rel="stylesheet">
<style>
  :root {
    --bg-light: #d2d2d2;
    --bg-dark: #a9a9a9;
    --card-white: #ffffff;
    --brand-blue: #1f74bf;
    --bright-blue: #1e98f5;
    --deep-blue: #1a64a8;
    --text-grey: #4a4a4a;
    --rule-grey: #c4c4c4;
  }
  * { margin: 0; padding: 0; box-sizing: border-box; }
  html, body { width: 1200px; height: 800px; overflow: hidden; }
  body {
    background: linear-gradient(135deg, var(--bg-dark), var(--bg-light));
    font-family: "Poppins", sans-serif;
    position: relative;
  }
  .card {
    position: absolute;
    top: 245px;
    width: 540px;
    height: 310px;
    overflow: hidden;
    box-shadow: 0 14px 30px rgba(0,0,0,0.28);
  }
  /* Front */
  .card-front {
    left: 45px;
    background: var(--card-white);
    border-bottom: 4px solid var(--brand-blue);
    display: flex;
    align-items: center;
  }
  .front-brand {
    width: 50%;
    display: flex;
    align-items: center;
    justify-content: center;
    gap: 10px;
  }
  .brand-mark {
    width: 14px; height: 14px;
    background: var(--brand-blue);
  }
  .brand-name {
    font-weight: 600;
    font-size: 25px;
    color: var(--brand-blue);
    white-space: nowrap;
  }
  .front-divider {
    width: 1px;
    height: 190px;
    background: var(--rule-grey);
  }
  .front-contact {
    width: 50%;
    padding-left: 34px;
  }
  .person-name {
    font-family: "Montserrat", sans-serif;
    font-weight: 800;
    font-size: 22px;
    color: var(--brand-blue);
    letter-spacing: 0.5px;
  }
  .person-title {
    font-size: 15px;
    color: var(--text-grey);
    margin-bottom: 22px;
  }
  .contact-list { list-style: none; }
  .contact-list li {
    display: flex;
    align-items: center;
    gap: 9px;
    font-size: 14px;
    color: var(--text-grey);
    line-height: 1.75;
  }
  .contact-list svg { width: 14px; height: 14px; fill: var(--brand-blue); flex: none; }
  .web-accent { color: var(--brand-blue); }
  /* Back */
  .card-back {
    left: 615px;
    background: var(--brand-blue);
  }
  .back-bands { position: absolute; inset: 0; }
  .back-brand {
    position: absolute;
    left: 44px;
    bottom: 46px;
    display: flex;
    align-items: center;
    gap: 10px;
  }
  .back-brand .brand-mark { background: var(--card-white); }
  .back-brand .brand-name { color: var(--card-white); font-size: 30px; }
</style>
</head>
<body>
  <section class="card card-front">
    <div class="front-brand">
      <span class="brand-mark"></span>
      <span class="brand-name">Tall Fern Roofing</span>
    </div>
    <div class="front-divider"></div>
    <div class="front-contact">
      <h1 class="person-name">MARCUS HALE</h1>
      <p class="person-title">Managing Director</p>
      <ul class="contact-list">
        <li>
          <svg viewBox="0 0 24 24"><path d="M6.6 10.8a15.1 15.1 0 0 0 6.6 6.6l2.2-2.2a1 1 0 0 1 1-.25 11.4 11.4 0 0 0 3.6.57 1 1 0 0 1 1 1V20a1 1 0 0 1-1 1A17 17 0 0 1 3 4a1 1 0 0 1 1-1h3.5a1 1 0 0 1 1 1c0 1.25.2 2.45.57 3.57a1 1 0 0 1-.25 1z"/></svg>
          044-987 654 321
        </li>
        <li>
          <svg viewBox="0 0 24 24"><path d="M2 5h20v14H2z" fill="none"/><path d="M2 5h20v2l-10 6L2 7zM2 9l10 6 10-6v10H2z"/></svg>
          hello@tallfern.com
        </li>
        <li>
          <svg viewBox="0 0 24 24"><path d="M12 2a10 10 0 1 0 0 20 10 10 0 0 0 0-20zm6.9 6h-2.9a15.6 15.6 0 0 0-1.4-3.6A8 8 0 0 1 18.9 8zM12 4c.8 1.2 1.5 2.5 1.9 4h-3.8c.4-1.5 1.1-2.8 1.9-4zM4.3 14a8.2 8.2 0 0 1 0-4h3.4a16.5 16.5 0 0 0 0 4zm.8 2h2.9c.3 1.3.8 2.5 1.4 3.6A8 8 0 0 1 5.1 16zM8 8H5.1a8 8 0 0 1 4.3-3.6C8.8 5.5 8.3 6.7 8 8zm4 12c-.8-1.2-1.5-2.5-1.9-4h3.8c-.4 1.5-1.1 2.8-1.9 4zm2.3-6H9.7a14.7 14.7 0 0 1 0-4h4.6a14.7 14.7 0 0 1 0 4zm.3 5.6c.6-1.1 1.1-2.3 1.4-3.6h2.9a8 8 0 0 1-4.3 3.6zm1.7-5.6a16.5 16.5 0 0 0 0-4h3.4a8.2 8.2 0 0 1 0 4z"/></svg>
          <span>www.<span class="web-accent">tallfernroofing</span>.com</span>
        </li>
      </ul>
    </div>
  </section>

  <section class="card card-back">
    <svg class="back-bands" viewBox="0 0 540 310" preserveAspectRatio="none" aria-hidden="true">
      <polygon points="0,0 540,0 540,150 0,40" fill="var(--bright-blue)"/>
      <polygon points="0,40 540,150 540,165 0,55" fill="var(--deep-blue)"/>
      <polygon points="0,0 540,0 540,20 0,0" fill="var(--deep-blue)"/>
    </svg>
    <div class="back-brand">
      <span class="brand-mark"></span>
      <span class="brand-name">Tall Fern Roofing</span>
    </div>
  </section>
</body>
</html>
```